Create a webpage for TradeKickback

TradeKickback.com is a new forex rebate site we wish to launch in parallel to our sister site refundlegion.com

Were looking for a webpage with a modern, clean, corporate professional feel, that shows we are a reliable trustworthy company.

Our company offers commission to its registered users based on the volume of trading activity. Essentially they receive a payment everytime they transact irrespective of whether that trade makes money or loses money.

Blue and green are the colours we have decided on so but we are still open to other colour schemes as long as they have a refreshing clean and smart appearance.

Target Market(s)

Online retail forex traders

Industry/Entity Type

Trade

Requirements
Must have
• We are not looking for many pages but at a minimum the refund legion.com website can guide you.

Another site of interest;
PayBright Markets

```html
<!DOCTYPE html>
<html lang="en">
<head>
<meta charset="utf-8">
<title>TradeKickback.com</title>
<link rel="stylesheet" href="https://fonts.googleapis.com/css2?family=Arimo:wght@400;700&family=Arvo:wght@700&family=Open+Sans:wght@300;400&display=swap">
<style>
:root{
  --navy:#123a6a;
  --navy-dark:#0d2a52;
  --navy-top:#1a4478;
  --green:#6aa82a;
  --green-dark:#4f8a18;
  --green-light:#7cbd34;
  --heading-green:#5c9c1e;
  --heading-blue:#1f5b98;
  --text:#5a5a5a;
  --muted:#9a9a9a;
  --rule:#dedede;
  --hero:#eef4f8;
  --footer:#2c2c2c;
  --footer-text:#bdbdbd;
  --white:#ffffff;
}
*{box-sizing:border-box;margin:0;padding:0}
html,body{width:882px;height:1200px;overflow:hidden;background:var(--white)}
body{position:relative;font-family:"Arimo",Arial,sans-serif;color:var(--text);font-size:11px}
a{color:inherit;text-decoration:none}

.site-header{position:absolute;left:0;top:0;width:882px;height:78px;background:linear-gradient(var(--navy-top),var(--navy-dark))}
.brand{position:absolute;left:72px;top:18px;font-family:"Open Sans",sans-serif;font-weight:300;font-size:35px;color:var(--white);letter-spacing:-0.5px}
.brand small{font-size:19px}
.account{position:absolute;right:74px;top:28px;display:flex;gap:5px}
.account a{display:block;height:23px;line-height:23px;padding:0 8px;background:linear-gradient(#f1f1f1,#d2d2d2);border-radius:2px;color:#444;font-size:11px}

.main-nav{position:absolute;left:0;top:78px;width:882px;height:39px;background:linear-gradient(var(--green-light),var(--green));border-bottom:1px solid var(--green-dark)}
.main-nav ul{position:absolute;left:75px;top:0;list-style:none;display:flex;height:39px}
.main-nav li{height:39px;line-height:39px;padding:0 13px;color:var(--white);font-weight:700;font-size:11.5px;border-right:1px solid var(--green-dark)}
.main-nav li.active{background:var(--green-dark)}
.search{position:absolute;left:641px;top:8px;width:163px;height:23px;background:var(--white);font-size:9.5px;color:#777;line-height:23px;padding-left:10px}
.search svg{position:absolute;right:7px;top:5px}

.hero{position:absolute;left:0;top:117px;width:882px;height:351px;background:var(--hero);border-bottom:1px solid #d0d6da}
.hero h1{position:absolute;left:0;width:882px;top:28px;text-align:center;font-family:"Arvo",serif;font-size:21px;color:#7a7a7a}
.hero-art{position:absolute;left:150px;top:70px;width:582px;height:270px;background:radial-gradient(ellipse at center,#ffffff 0%,#e4ebf0 70%,var(--hero) 100%)}

.content{position:absolute;left:75px;top:490px;width:512px}
.content h2{color:var(--heading-green);font-size:18px;font-weight:700}
.content h3{color:var(--heading-green);font-size:15.5px;font-weight:400}
.content p{font-size:10.6px;line-height:18.4px;text-align:justify}
.intro p{margin-top:10px}
.rule{height:1px;background:var(--rule);margin-left:-2px}
.how h3{margin-top:20px}
.how p{margin-top:8px}
.feature{display:flex;gap:15px;margin-top:12px}
.video{width:222px;height:138px;flex:none;position:relative;background:linear-gradient(110deg,#8c8c8c,#b9b9b9 40%,#3d6f92 70%,#8a8a8a)}
.video svg{position:absolute;left:86px;top:43px}
.feature-text p{margin-top:-3px}
.btn-more{display:inline-block;margin-top:7px;height:24px;line-height:24px;padding:0 8px;background:linear-gradient(var(--green-light),var(--green-dark));color:var(--white);font-size:11px;border-radius:2px}

.partners{margin-top:30px}
.partner-row{display:flex;justify-content:space-between;align-items:center;height:46px}
.partner-row span{font-weight:700;font-size:13.5px;color:#4b5560}
.partners .rule{margin-top:6px}
.partners .rule.top{margin-top:0;margin-bottom:8px}

.ad{position:absolute;left:150px;top:1053px;width:359px;height:47px;border:1px solid #1a6bb0;background:#1a5fa3;display:flex}
.ad-photo{width:52px;height:100%;background:linear-gradient(#6a4a3a,#b07a5a)}
.ad-copy{flex:1;color:var(--white);font-weight:700;font-size:11px;line-height:13px;padding:7px 0 0 8px}
.ad-badge{width:110px;background:var(--white);color:#1a5fa3;padding:6px 6px;text-align:center}
.ad-badge b{display:block;font-size:14px}
.ad-badge small{display:block;font-size:6px;color:#555;margin-top:3px}

.sidebar{position:absolute;left:617px;top:492px;width:192px}
.sidebar h2{color:var(--heading-blue);font-size:17.5px;font-weight:400}
.pager{position:absolute;right:0;top:5px;display:flex;gap:2px}
.pager span{width:12px;height:12px;border-radius:50%;background:#e6e6e6;font-size:8px;line-height:12px;text-align:center;color:#666}
.news-item{margin-top:14px}
.news-title{height:21px;line-height:21px;background:var(--navy);color:var(--white);font-size:12px;padding-left:5px}
.news-item p{font-size:10.6px;line-height:15px;padding:8px 3px 0;color:#666}
.news-item time{display:block;color:var(--muted);font-size:10.3px;padding:5px 3px 0}
.sidebar .rule{margin:13px 0 0}
.sidebar h2.calc-title{margin-top:22px;font-size:16px;white-space:nowrap;letter-spacing:-0.2px}
.calc{margin-top:8px;background:linear-gradient(var(--navy),var(--navy-dark));width:193px;height:251px;position:relative;color:var(--white)}
.calc label{position:absolute;font-size:9px}
.field{position:absolute;height:23px;background:var(--white);color:#777;font-size:9px;line-height:23px;padding-left:9px}
.field svg{position:absolute;right:4px;top:8px}
.calc-btn{position:absolute;left:93px;top:78px;width:93px;height:23px;background:var(--green);font-size:10px;line-height:23px;padding-left:6px}
.calc-btn svg{position:absolute;right:6px;top:8px}
.earnings{position:absolute;left:4px;top:115px;width:185px;height:90px;background:#f4f4f4;color:#555;padding:10px 0 0 12px}
.earnings h4{font-size:11.5px;font-weight:400;color:var(--navy)}
.earnings p{font-size:9.5px;line-height:18.4px}
.earnings h4+p{margin-top:4px}
.calc-note{position:absolute;left:16px;top:216px;font-size:11px;line-height:14px}

.site-footer{position:absolute;left:0;top:1129px;width:882px;height:71px;background:var(--footer);color:var(--footer-text)}
.footer-nav{position:absolute;left:75px;top:18px;font-size:9.5px;display:flex}
.footer-nav a:not(:last-child)::after{content:"|";margin:0 9px}
.copyright{position:absolute;left:75px;top:44px;font-size:9.5px}
.social{position:absolute;left:712px;top:26px;display:flex;gap:6px}
.social span{width:20px;height:20px;border-radius:50%;background:#5f5f5f}
</style>
</head>
<body>
<header class="site-header">
  <div class="brand">TradeKickback<small>.com</small></div>
  <nav class="account"><a href="#">REGISTER</a><a href="#">LOGIN</a></nav>
</header>

<nav class="main-nav">
  <ul>
    <li class="active">About us</li><li>How it works</li><li>Compare</li><li>Products</li><li>Promotions</li><li>Blog</li><li>Contact us</li>
  </ul>
  <div class="search">Search
    <svg width="12" height="12" viewBox="0 0 12 12"><circle cx="4.5" cy="4.5" r="3.3" fill="none" stroke="#222" stroke-width="1.8"/><line x1="7" y1="7" x2="11" y2="11" stroke="#222" stroke-width="2.4"/></svg>
  </div>
</nav>

<section class="hero">
  <h1>Your erade make money or lose you can get a commission</h1>
  <div class="hero-art" role="img" aria-label="Illustration of three white 3D figures passing gold coins over soft grey curved lines"></div>
</section>

<main class="content">
  <section class="intro">
    <h2>Welcome to TradeKickback</h2>
    <p>Sed varius, mi facilisis eleifend viverra, enim eros faucibus risus, eget venenatis ante sem a magna. In hen drerit vulputate fermentum. Duis eu volutpat sapien, sit amet ultrices nunc. Cras malesuada, turpis quis sodales pulvinar, quam lacus venenatis ipsum, euismod vehicula ipsum lacus porta arcu. Quisque sagittis massa id ipsum fermentum, nec consequat tortor molestie. Sed a lorem quis velit tempor dapibus. Maecenas congue scelerisque venenatis. Vivamus porttitor vulputate vestibulum.</p>
  </section>
  <div class="rule" style="margin-top:20px"></div>
  <section class="how">
    <h3>How it works</h3>
    <p>Nam fringilla dapibus sem, et condimentum sem commodo quis. In non convallis libero, quis porttitor ligula. Morbi id dolor mollis, aliquam nibh non, fringilla sem. Pellentesque habitant morbi tristique senectus et netus et malesuada fames ac turpis egestas. Integer in orci pellentesque, condimentum nisi et, varius nibh.</p>
    <div class="feature">
      <div class="video" role="img" aria-label="Video thumbnail of financial charts and a globe">
        <svg width="52" height="52" viewBox="0 0 52 52"><circle cx="26" cy="26" r="23" fill="none" stroke="#fff" stroke-width="3.5"/><path d="M20 15 L37 26 L20 37 Z" fill="#fff"/></svg>
      </div>
      <div class="feature-text">
        <p>Nam fringilla dapibus, et condimentum sem commodo quis. In non convallis libero, quis porttitor ligula. Morbi id dolor mollis, aliquam nibh non, fringilla sem. Pellentesque habitant morbi tristique senectus et netus et malesuada fames ac turpis egestas. Integer in orci pellentesque, con dimentum nisi et, varius nibh.</p>
        <a class="btn-more" href="#">Know more</a>
      </div>
    </div>
  </section>
  <section class="partners">
    <div class="rule top"></div>
    <div class="partner-row"><span>Orchardline</span><span>Pinemark</span><span>Quillon</span><span>Harbory</span><span>Strata Nine</span><span>Vellum Co</span></div>
    <div class="partner-row"><span>Brightwick</span><span>Tessaro</span><span>Meridane</span><span>Solvoy</span><span>Corvane</span><span>Northpeak</span></div>
    <div class="rule"></div>
  </section>
</main>

<aside class="ad">
  <div class="ad-photo" role="img" aria-label="Photo of a child holding an apple"></div>
  <div class="ad-copy">Who can help your family eat<br>right to stay at a healthy weight?</div>
  <div class="ad-badge"><b>Fit Families</b><small>Community Nutrition Initiative</small></div>
</aside>

<aside class="sidebar">
  <h2>Latest News</h2>
  <div class="pager"><span>‹</span><span>›</span></div>
  <article class="news-item"><div class="news-title">Cras malesuada, turpis</div><p>Aliquam molestie turpis, vitaet euismod odio imperdiet eget.</p><time>December 11, 2013</time></article>
  <article class="news-item"><div class="news-title">Cras malesuada, turpis</div><p>Aliquam molestie turpis, vitaet euismod odio imperdiet eget.</p><time>December 11, 2013</time></article>
  <article class="news-item"><div class="news-title">Cras malesuada, turpis</div><p>Aliquam molestie turpis, vitaet euismod odio imperdiet eget.</p><time>December 11, 2013</time></article>
  <div class="rule"></div>
  <h2 class="calc-title">TradeKickback Calculator</h2>
  <div class="calc">
    <label style="left:8px;top:10px">Volume</label>
    <label style="left:93px;top:10px"># traded per day</label>
    <div class="field" style="left:8px;top:24px;width:78px">Lot Size<svg width="10" height="7"><path d="M0 0H10L5 7Z" fill="#888"/></svg></div>
    <div class="field" style="left:93px;top:24px;width:93px"></div>
    <label style="left:8px;top:63px">Rebate Offered</label>
    <div class="field" style="left:8px;top:78px;width:78px">Lot Size<svg width="10" height="7"><path d="M0 0H10L5 7Z" fill="#888"/></svg></div>
    <div class="calc-btn">Calculate Now<svg width="10" height="7"><path d="M0 0H10L5 7Z" fill="#fff"/></svg></div>
    <div class="earnings">
      <h4>Earnings</h4>
      <p>Monthly Cash Earnings: $0.00</p>
      <p>Yearly Cash Earnings: $0.00</p>
      <p>Yearly Pip Earnings: 0.00 Pips</p>
    </div>
    <p class="calc-note">* Figures based on 21 day<br>&nbsp; trading month</p>
  </div>
</aside>

<footer class="site-footer">
  <nav class="footer-nav"><a href="#">Home</a><a href="#">About us</a><a href="#">How it works</a><a href="#">Compare</a><a href="#">Products</a><a href="#">Promotions</a><a href="#">Blog</a><a href="#">Contact us</a></nav>
  <p class="copyright">Copyright © 2013 &nbsp;TradeKickback. &nbsp;All rights reserved.</p>
  <div class="social"><span></span><span></span><span></span><span></span></div>
</footer>
</body>
</html>
```